Computer consultant business card

Bexil Software is a newly started computer consulting company. It's a small one-man company that provides mostly Vornix applications but also websites in collaboration with designers. I'm running this company on the side of full time university studies.

I want the final design to be clean and memorable. Be creative! :)

Some inspiration:
http://www.pixelmarta.com/design/48317
http://www.pixelmarta.com/design/2739164/business-card-design-by-frostlynk
http://www.pixelmarta.com/design/604281/business-card-design-by-koralind-vestrabanu

See attachment for my company logo.
Updates

I would like to thank everyone for submitting! I'll need a couple of days to review and ultimately select a design.

Target Market(s)

Non-technical entrepreneurs and small companies.

Industry/Entity Type

University

Requirements
Must have
• My company logo.
In any way, both colors from my logo.
First- and last name, e-mail and phone number.
Double-sided design.
Nice to have
• Something creative with the symbol in my logo

```html
<!DOCTYPE html>
<html lang="en">
<head>
<meta charset="utf-8">
<title>Bexil Software – Business Card</title>
<link href="https://fonts.googleapis.com/css2?family=Exo+2:wght@400;500&family=Tinos&display=swap" rel="stylesheet">
<style>
  :root {
    --page: #e7e4e0;
    --card-dark: #2c3640;
    --card-dark-deep: #232b33;
    --card-light: #f3f3f3;
    --brand-grey: #4a4a4d;
    --brand-blue: #5b86c6;
    --text-light: #d9dde2;
    --text-muted: #b7bec6;
  }
  * { margin: 0; padding: 0; box-sizing: border-box; }
  html, body {
    width: 1200px; height: 900px; overflow: hidden;
    background: var(--page);
    font-family: "Exo 2", sans-serif;
  }
  .card {
    position: absolute;
    left: 250px;
    width: 700px; height: 400px;
    border-radius: 4px;
    overflow: hidden;
    box-shadow: 0 6px 18px rgba(0,0,0,0.18);
  }
  .card--back { top: 470px; background: linear-gradient(180deg, var(--card-dark), var(--card-dark-deep)); }
  .card--front { top: 50px; background: var(--card-dark); }

  /* front */
  .front__top {
    position: absolute; inset: 0 0 auto 0; height: 178px;
    background: var(--card-light);
    display: flex; align-items: center; justify-content: center;
  }
  .front__rule {
    position: absolute; left: 0; right: 0; top: 178px; height: 3px;
    background: var(--brand-blue);
  }
  .front__stitch {
    position: absolute; left: 0; right: 0; top: 186px;
    border-top: 1px dashed rgba(255,255,255,0.35);
  }
  .brand {
    display: flex; align-items: center; gap: 22px;
  }
  .brand__dot {
    width: 58px; height: 58px; border-radius: 50%;
    background: var(--brand-blue);
  }
  .brand__name {
    font-family: "Exo 2", sans-serif;
    font-weight: 500; font-size: 88px; line-height: 1;
    color: var(--brand-grey);
    letter-spacing: 2px;
  }
  .person {
    position: absolute; left: 48px; top: 232px;
  }
  .person__name {
    font-family: "Tinos", serif;
    font-size: 30px; color: var(--brand-blue);
  }
  .person__role {
    margin-top: 2px; padding-left: 18px;
    font-size: 14px; color: var(--text-light); letter-spacing: 0.5px;
  }
  .contacts {
    position: absolute; left: 400px; top: 232px;
    list-style: none; color: var(--text-light);
    font-size: 16px; letter-spacing: 0.6px;
  }
  .contacts li { display: flex; align-items: center; gap: 12px; height: 28px; }
  .contacts svg { width: 18px; height: 18px; flex: none; }
  .contacts .contacts__address { padding-left: 0; color: var(--text-muted); margin-left: -14px; }

  /* back */
  .back__band { position: absolute; inset: 0; }
  .back__brand {
    position: absolute; left: 350px; top: 200px;
    transform: translate(-50%, -50%) rotate(-21deg);
  }
  .back__brand .brand__name { font-size: 80px; }
  .back__brand .brand__dot { width: 52px; height: 52px; }
</style>
</head>
<body>

<section class="card card--front" aria-label="Business card front">
  <div class="front__top">
    <div class="brand">
      <span class="brand__dot"></span>
      <span class="brand__name">bexil</span>
    </div>
  </div>
  <div class="front__rule"></div>
  <div class="front__stitch"></div>

  <div class="person">
    <p class="person__name">Alden Marsh</p>
    <p class="person__role">Genral Manager</p>
  </div>

  <ul class="contacts">
    <li>
      <svg viewBox="0 0 24 24" fill="#5b86c6"><path d="M6.6 10.8a15 15 0 0 0 6.6 6.6l2.2-2.2c.3-.3.7-.4 1-.2 1.1.4 2.3.6 3.6.6.6 0 1 .4 1 1V20c0 .6-.4 1-1 1A17 17 0 0 1 3 4c0-.6.4-1 1-1h3.5c.6 0 1 .4 1 1 0 1.3.2 2.5.6 3.6.1.3 0 .7-.2 1z"/></svg>
      <span>+1 555 204 718</span>
    </li>
    <li>
      <svg viewBox="0 0 24 24" fill="#5b86c6"><path d="M2 5h20v14H2z" opacity=".9"/><path d="M2 5l10 8 10-8" fill="none" stroke="#2c3640" stroke-width="1.8"/></svg>
      <span>info@bexilsoft.com</span>
    </li>
    <li>
      <svg viewBox="0 0 24 24" fill="none" stroke="#5b86c6" stroke-width="2.4" stroke-linecap="round"><path d="M10 14a4 4 0 0 0 5.7 0l3-3a4 4 0 0 0-5.7-5.7l-1 1"/><path d="M14 10a4 4 0 0 0-5.7 0l-3 3a4 4 0 0 0 5.7 5.7l1-1"/></svg>
      <span>www.bexilsoft.com</span>
    </li>
    <li class="contacts__address">48210 Orrin St Calder, CA 1174</li>
  </ul>
</section>

<section class="card card--back" aria-label="Business card back">
  <svg class="back__band" viewBox="0 0 700 400" preserveAspectRatio="none">
    <polygon points="0,300 700,32 700,150 0,418" fill="#f3f3f3"/>
  </svg>
  <div class="brand back__brand">
    <span class="brand__dot"></span>
    <span class="brand__name">bexil</span>
  </div>
</section>

</body>
</html>
```